web page look and feel - B2B enterprise application

We have an enterprise application with 10 to 15 core pages and several supporting pages or popups. To start, we want the graphical design of the Users, Roles and Data Source pages and their supporting popups, wizards, etc. to be made beautiful. That is around 10 pages in total. There is a fair amount of redundancy among the pages. I have attached 5 screenshots. We very much want the pages to project a premium feel. That is absolutely essential. The color scheme is blue and sometimes yellow (only if it makes the page look better) plus black, gray and white. If the design of these screens goes well, we would expand the project to continue with other pages. The core of what we are looking for is graphic in nature but we are open to workflow suggestions if you have them. The Roles screen needs some improvements to the layout. I am looking for everything that includes icons, fonts, spacing, etc. I assume getting to the final design will take some back and forth with multiple revisions.

Target Market(s)

Large Enterprises

Number of Pages Required

5+ page

Requirements
Must have
• Premium feel

```html
<!DOCTYPE html>
<html lang="en">
<head>
<meta charset="utf-8">
<title>Users</title>
<link rel="stylesheet" href="https://fonts.googleapis.com/css2?family=Exo+2:wght@400;500;600&family=Montserrat:wght@400;500&display=swap">
<style>
:root{
  --navy:#0a213e;
  --brand-a:#0a6ee0;
  --brand-b:#0a2a9e;
  --blue:#1f7fe6;
  --blue-head:#2e8ded;
  --blue-soft:#8ec0f2;
  --line:#bcd8f3;
  --page:#ececec;
  --white:#ffffff;
  --ink:#3a3f47;
  --muted:#9aa6b4;
}
*{box-sizing:border-box;margin:0;padding:0}
html,body{width:1200px;height:786px;overflow:hidden}
body{font-family:"Exo 2",sans-serif;background:var(--page);position:relative;color:var(--ink)}
.brand{position:absolute;left:0;top:0;width:300px;height:80px;background:linear-gradient(90deg,var(--brand-a),var(--brand-b));display:flex;align-items:center;padding-left:44px;gap:10px}
.brand-dot{width:26px;height:26px;border-radius:50%;background:var(--white)}
.brand-name{font-family:"Exo 2",sans-serif;font-weight:600;font-size:26px;color:var(--white)}
.sidebar{position:absolute;left:0;top:80px;width:300px;height:706px;background:var(--navy);color:var(--white)}
.profile{position:absolute;left:40px;top:20px;display:flex;gap:10px}
.avatar{width:40px;height:40px;border-radius:50%;background:radial-gradient(circle at 50% 40%,#c89a7c,#5b4436);border:2px solid #e8e8e8}
.profile-name{font-family:"Montserrat",sans-serif;font-size:15px;margin-top:0}
.profile-mail{font-family:"Montserrat",sans-serif;font-size:12px;color:#8b97a8;margin-top:3px}
.divider{position:absolute;left:20px;top:80px;width:260px;height:1px;background:#2e4463}
.nav{position:absolute;left:40px;top:101px;width:225px;list-style:none}
.nav li{height:32px;display:flex;align-items:center;font-size:15px;position:relative}
.nav svg{width:18px;height:18px;margin-right:14px;fill:var(--white)}
.nav .chev{position:absolute;right:0;font-size:13px}
.clock-row{position:absolute;left:30px;right:30px;top:578px;display:flex;justify-content:space-between;font-size:15px;font-weight:500}
.clock-row span{display:flex;align-items:center;gap:10px}
.topbar{position:absolute;left:300px;top:0;width:900px;height:80px;background:var(--white);border-bottom:1px solid var(--blue)}
.topbar svg{position:absolute;fill:var(--blue)}
.account{position:absolute;left:742px;top:28px;display:flex;align-items:center;gap:12px;font-size:17px;font-weight:600;color:var(--blue)}
.title{position:absolute;left:328px;top:114px;font-family:"Montserrat",sans-serif;font-size:31px;font-weight:400;color:#333}
.search{position:absolute;left:1092px;top:163px;font-size:16px;color:var(--blue-soft);display:flex;align-items:center;gap:8px}
.add{position:absolute;left:1105px;top:204px;width:64px;height:28px;background:var(--blue);color:var(--white);font-size:16px;display:flex;align-items:center;justify-content:center;gap:5px;box-shadow:0 2px 8px rgba(31,127,230,.5)}
.users{position:absolute;left:330px;top:262px;width:840px;border-collapse:collapse;background:var(--white);font-size:16px}
.users th{background:var(--blue-head);color:var(--white);font-weight:500;height:39px;border:1px solid var(--line);border-top:none}
.users td{height:39px;text-align:center;border:1px solid var(--line);color:#555}
.users .toggle{width:40px;color:var(--blue);font-size:13px}
.actions{display:flex;justify-content:center;gap:8px}
.act{width:20px;height:20px;background:var(--blue);display:flex;align-items:center;justify-content:center}
.act svg{width:13px;height:13px;fill:none;stroke:var(--white);stroke-width:1.5}
.pager{position:absolute;left:677px;top:596px;display:flex;align-items:center;gap:6px;font-size:16px;color:var(--blue-soft)}
.pager .current{color:var(--blue)}
.pager .size{margin-left:14px;background:var(--blue-soft);color:var(--white);padding:0 5px;font-weight:600}
</style>
</head>
<body>
<header class="brand"><span class="brand-dot"></span><span class="brand-name">Norvale Data</span></header>

<aside class="sidebar">
  <div class="profile">
    <div class="avatar" role="img" aria-label="User profile photo"></div>
    <div><div class="profile-name">Dana Moreau</div><div class="profile-mail">dana.moreau@mailbox.dev</div></div>
  </div>
  <div class="divider"></div>
  <ul class="nav">
    <li><svg viewBox="0 0 16 16"><circle cx="8" cy="4.5" r="3.5"/><path d="M2 16c0-4 2.5-6 6-6s6 2 6 6z"/></svg>User<span class="chev">&#8250;</span></li>
    <li><svg viewBox="0 0 16 16"><rect x="0" y="1" width="16" height="4"/><rect x="0" y="7" width="16" height="4"/><rect x="7" y="12" width="2" height="3"/><rect x="2" y="14" width="12" height="1.5"/></svg>Data Source<span class="chev">&#8250;</span></li>
    <li><svg viewBox="0 0 16 16"><rect x="0" y="0" width="7" height="16"/><rect x="9" y="0" width="7" height="7"/><rect x="9" y="9" width="7" height="7"/></svg>Data Sets</li>
    <li><svg viewBox="0 0 16 16"><rect x="0" y="0" width="6" height="16"/><rect x="8" y="1" width="8" height="2"/><rect x="8" y="5" width="8" height="2"/><rect x="8" y="9" width="8" height="2"/><rect x="8" y="13" width="8" height="2"/></svg>Rule Sets</li>
    <li><svg viewBox="0 0 16 16"><path d="M8 0a8 8 0 1 0 0 16A8 8 0 0 0 8 0zm0 1.6a6.4 6.4 0 1 1 0 12.8A6.4 6.4 0 0 1 8 1.6zM7.2 3.5h1.6v4.2l3 1.8-.8 1.3-3.8-2.3z"/></svg>Schedule</li>
    <li><svg viewBox="0 0 16 16" style="fill:none;stroke:#fff;stroke-width:1.6"><path d="M2.5 7A5.5 5.5 0 0 1 13 5.5M13.5 9A5.5 5.5 0 0 1 3 10.5"/><path d="M13 2v3.5H9.5M3 14v-3.5h3.5"/></svg>Metadata Import/Export<span class="chev">&#8250;</span></li>
  </ul>
  <div class="clock-row">
    <span><svg width="26" height="28" viewBox="0 0 26 28" fill="none" stroke="#fff" stroke-width="2"><rect x="2" y="4" width="22" height="22" rx="2"/><path d="M2 10h22M7 1v5M13 1v5M19 1v5"/><text x="9" y="23" fill="#fff" stroke="none" font-size="12" font-family="Exo 2,sans-serif" font-weight="600">5</text></svg>July 05</span>
    <span><svg width="26" height="26" viewBox="0 0 26 26" fill="none" stroke="#fff" stroke-width="2"><circle cx="13" cy="13" r="11"/><path d="M13 6v7l4 3"/></svg>18:36</span>
  </div>
</aside>

<div class="topbar">
  <svg style="left:30px;top:31px" width="18" height="16" viewBox="0 0 18 16"><rect y="1" width="18" height="3"/><rect y="7" width="18" height="3"/><rect y="13" width="18" height="3"/></svg>
  <svg style="left:493px;top:30px" width="26" height="20" viewBox="0 0 26 20"><path d="M13 2A12 12 0 0 0 1 14h3A9 9 0 0 1 22 14h3A12 12 0 0 0 13 2z"/><path d="M12 14l6-7 1 1-5 7z"/></svg>
  <svg style="left:543px;top:28px" width="26" height="26" viewBox="0 0 26 26"><path d="M2 23l15-15 2 2L4 25z"/><circle cx="21" cy="3" r="1.3"/><circle cx="24" cy="7" r="1.3"/><circle cx="17" cy="2" r="1"/></svg>
  <svg style="left:593px;top:27px" width="26" height="26" viewBox="0 0 26 26"><circle cx="13" cy="13" r="13"/><text x="13" y="19" fill="#fff" font-size="17" font-weight="700" text-anchor="middle" font-family="Exo 2,sans-serif">?</text></svg>
  <svg style="left:643px;top:27px" width="26" height="26" viewBox="0 0 26 26"><circle cx="9" cy="15" r="7"/><circle cx="19" cy="6" r="5"/><circle cx="9" cy="15" r="2.5" fill="#fff"/><circle cx="19" cy="6" r="1.8" fill="#fff"/></svg>
  <div class="account"><svg style="position:static" width="20" height="24" viewBox="0 0 20 24"><circle cx="10" cy="6" r="6"/><path d="M0 24c0-6 4-10 10-10s10 4 10 10z"/></svg>Dana Moreau<span style="font-size:12px;margin-left:4px">&#8964;</span></div>
</div>

<main>
  <h1 class="title">Users</h1>
  <div class="search">Search <svg width="22" height="22" viewBox="0 0 22 22" fill="none" stroke="#8ec0f2" stroke-width="2"><circle cx="9" cy="9" r="7.5"/><path d="M14.5 14.5l6 6"/></svg></div>
  <div class="add"><svg width="15" height="15" viewBox="0 0 16 16" fill="none" stroke="#fff" stroke-width="1.4"><circle cx="8" cy="8" r="7"/><path d="M8 4.5v7M4.5 8h7"/></svg>Add</div>

  <table class="users">
    <thead><tr><th></th><th>First Name</th><th>Last Name</th><th>Username</th><th>Email</th><th>Status</th><th>Edit</th></tr></thead>
    <tbody>
      <tr><td class="toggle">&#8964;</td><td>Test</td><td>Test</td><td>test.1</td><td>test@sample.dev</td><td>Active</td><td><div class="actions"><span class="act"><svg viewBox="0 0 14 14"><path d="M3 10l1-3 6-6 2 2-6 6zM2 13h10"/></svg></span><span class="act"><svg viewBox="0 0 14 14"><rect x="4" y="4" width="8" height="9"/><path d="M2 10V1h7"/></svg></span><span class="act"><svg viewBox="0 0 14 14"><path d="M2 3h10M5 3V1h4v2M3 3l1 10h6l1-10M6 5v6M8 5v6"/></svg></span></div></td></tr>
      <tr><td class="toggle">&#8964;</td><td>Test</td><td>Test</td><td>test.1</td><td>test@sample.dev</td><td>Active</td><td><div class="actions"><span class="act"><svg viewBox="0 0 14 14"><path d="M3 10l1-3 6-6 2 2-6 6zM2 13h10"/></svg></span><span class="act"><svg viewBox="0 0 14 14"><rect x="4" y="4" width="8" height="9"/><path d="M2 10V1h7"/></svg></span><span class="act"><svg viewBox="0 0 14 14"><path d="M2 3h10M5 3V1h4v2M3 3l1 10h6l1-10M6 5v6M8 5v6"/></svg></span></div></td></tr>
      <tr><td class="toggle">&#8964;</td><td>Test</td><td>Test</td><td>test.1</td><td>test@sample.dev</td><td>Active</td><td><div class="actions"><span class="act"><svg viewBox="0 0 14 14"><path d="M3 10l1-3 6-6 2 2-6 6zM2 13h10"/></svg></span><span class="act"><svg viewBox="0 0 14 14"><rect x="4" y="4" width="8" height="9"/><path d="M2 10V1h7"/></svg></span><span class="act"><svg viewBox="0 0 14 14"><path d="M2 3h10M5 3V1h4v2M3 3l1 10h6l1-10M6 5v6M8 5v6"/></svg></span></div></td></tr>
      <tr><td class="toggle">&#8964;</td><td>Test</td><td>Test</td><td>test.1</td><td>test@sample.dev</td><td>Active</td><td><div class="actions"><span class="act"><svg viewBox="0 0 14 14"><path d="M3 10l1-3 6-6 2 2-6 6zM2 13h10"/></svg></span><span class="act"><svg viewBox="0 0 14 14"><rect x="4" y="4" width="8" height="9"/><path d="M2 10V1h7"/></svg></span><span class="act"><svg viewBox="0 0 14 14"><path d="M2 3h10M5 3V1h4v2M3 3l1 10h6l1-10M6 5v6M8 5v6"/></svg></span></div></td></tr>
      <tr><td class="toggle">&#8964;</td><td>Test</td><td>Test</td><td>test.1</td><td>test@sample.dev</td><td>Active</td><td><div class="actions"><span class="act"><svg viewBox="0 0 14 14"><path d="M3 10l1-3 6-6 2 2-6 6zM2 13h10"/></svg></span><span class="act"><svg viewBox="0 0 14 14"><rect x="4" y="4" width="8" height="9"/><path d="M2 10V1h7"/></svg></span><span class="act"><svg viewBox="0 0 14 14"><path d="M2 3h10M5 3V1h4v2M3 3l1 10h6l1-10M6 5v6M8 5v6"/></svg></span></div></td></tr>
      <tr><td class="toggle">&#8964;</td><td>Test</td><td>Test</td><td>test.1</td><td>test@sample.dev</td><td>Active</td><td><div class="actions"><span class="act"><svg viewBox="0 0 14 14"><path d="M3 10l1-3 6-6 2 2-6 6zM2 13h10"/></svg></span><span class="act"><svg viewBox="0 0 14 14"><rect x="4" y="4" width="8" height="9"/><path d="M2 10V1h7"/></svg></span><span class="act"><svg viewBox="0 0 14 14"><path d="M2 3h10M5 3V1h4v2M3 3l1 10h6l1-10M6 5v6M8 5v6"/></svg></span></div></td></tr>
    </tbody>
  </table>

  <nav class="pager"><span>&#8249;</span><span class="current">1</span><span>2</span><span>3</span><span>4</span><span>&#8250;</span><span class="size">20 &#711;</span></nav>
</main>
</body>
</html>
```